Casino with the 'highest winning percentage' needs a stationery design

This is for a casino in Colombo, Sri Lanka and we need a stationery design for business card, letter head and envelope.

Should be very professional, simple and elegant without fancy fonts

Reason: Not fully satisfied with the designs. Need more designs.

Business

• 1. card deck symbol 'CLUBS' in red, or black

2. name in BLOCK CAPITAL LETTERS

3. Preferred font colours are black, white or red

4. Prefer 'professional /elegant' fonts
• SHOULD NOT HAVE ANY OTHER SYMBOL EXCEPT 'CLUBS'

DO NOT PREFER ITALIC FONTS

```html
<!DOCTYPE html>
<html lang="en">
<head>
<meta charset="utf-8">
<title>Marlowe's Entertainment – Business Card</title>
<link href="https://fonts.googleapis.com/css2?family=Noto+Serif:wght@400;700&display=swap" rel="stylesheet">
<style>
  :root {
    --stage: #ece7e1;
    --card: #ffffff;
    --card-edge: #d6d1cb;
    --ink: #111111;
    --red: #d8273a;
    --black: #000000;
    --suit-warm: #f6dcd2;
    --suit-grey: #e2e2e2;
  }
  * { margin: 0; padding: 0; box-sizing: border-box; }
  html, body { width: 1200px; height: 372px; overflow: hidden; }
  body {
    background: var(--stage);
    font-family: "Noto Serif", Georgia, serif;
    color: var(--ink);
    position: relative;
  }
  .card {
    position: absolute;
    top: 31px;
    width: 556px;
    height: 317px;
    background: var(--card);
    border: 1px solid var(--card-edge);
    overflow: hidden;
  }
  .card--front { left: 31px; }
  .card--back { left: 613px; }

  /* front */
  .brand-mark {
    position: absolute;
    left: 34px; top: 46px;
    width: 72px; height: 72px;
    border-radius: 50%;
    background: var(--red);
  }
  .brand-name {
    position: absolute;
    left: 136px; top: 50px;
    font-weight: 700;
    font-size: 27px;
    line-height: 37px;
    letter-spacing: 0.5px;
    color: var(--ink);
  }
  .accent-band {
    position: absolute;
    left: 0; top: 160px;
    width: 15px; height: 131px;
    background: var(--red);
    border-radius: 0 14px 14px 0;
  }
  .accent-tab {
    position: absolute;
    right: 0; top: 182px;
    width: 18px; height: 89px;
    background: var(--black);
    border-radius: 14px 0 0 14px;
  }
  .contact-list {
    position: absolute;
    left: 28px; top: 193px;
    list-style: none;
    font-size: 13.5px;
    line-height: 20.6px;
  }
  .contact-list li { display: flex; align-items: center; gap: 8px; }
  .contact-list svg { width: 11px; height: 11px; flex: none; }
  .office {
    position: absolute;
    right: 25px; top: 217px;
    text-align: right;
    font-size: 13.5px;
    line-height: 19.5px;
  }
  .office__name { color: var(--red); font-weight: 700; }

  /* back */
  .back-title {
    position: absolute;
    left: 0; right: 0; top: 40px;
    text-align: center;
    font-weight: 700;
    letter-spacing: 1px;
  }
  .back-title__first { display: block; color: var(--red); font-size: 39px; line-height: 48px; }
  .back-title__second { display: block; color: var(--ink); font-size: 41px; line-height: 54px; }
  .suits-art {
    position: absolute;
    left: 44px; right: 34px; top: 156px;
    height: 92px;
    border-radius: 6px;
    background: linear-gradient(90deg, var(--suit-warm) 0%, var(--suit-warm) 45%, var(--suit-grey) 60%, var(--suit-grey) 100%);
    opacity: 0.7;
  }
  .tagline {
    position: absolute;
    left: 0; right: 0; top: 262px;
    text-align: center;
    color: var(--red);
    font-weight: 700;
    font-size: 15px;
    letter-spacing: 2.4px;
  }
</style>
</head>
<body>
  <section class="card card--front">
    <span class="brand-mark"></span>
    <h1 class="brand-name">MARLOWE’S<br>ENTERTAINMENT</h1>
    <span class="accent-band"></span>
    <span class="accent-tab"></span>
    <ul class="contact-list">
      <li><svg viewBox="0 0 12 12"><circle cx="6" cy="6" r="5.4" fill="none" stroke="#d8273a" stroke-width="1.2"/><path d="M4 3.2l1.2 1.4-.6.8c.4.8 1 1.4 1.8 1.8l.8-.6 1.4 1.2-.8 1c-2.2-.3-4.3-2.4-4.6-4.6z" fill="#d8273a"/></svg>+ 94 11 2458760</li>
      <li><svg viewBox="0 0 12 12"><rect x="3.2" y="0.8" width="5.6" height="10.4" rx="1" fill="#d8273a"/><rect x="4.2" y="2" width="3.6" height="5.5" fill="#fff"/></svg>+ 94 77 5550192</li>
      <li><svg viewBox="0 0 12 12"><rect x="1" y="5" width="10" height="5" rx="1" fill="#d8273a"/><rect x="3" y="1.5" width="6" height="4" fill="#d8273a"/><rect x="3" y="6.5" width="6" height="1.5" fill="#fff"/></svg>+ 94 11 5550148</li>
      <li><svg viewBox="0 0 12 12"><rect x="0.8" y="2.5" width="10.4" height="7" rx="1" fill="#d8273a"/><path d="M1.2 3l4.8 3.6L10.8 3" fill="none" stroke="#fff" stroke-width="1"/></svg>info@marlowescolombo.com</li>
      <li><svg viewBox="0 0 12 12"><circle cx="6" cy="6" r="5.2" fill="#d8273a"/><path d="M0.8 6h10.4M6 0.8v10.4M6 0.8c-2.4 2.6-2.4 7.8 0 10.4M6 0.8c2.4 2.6 2.4 7.8 0 10.4" fill="none" stroke="#fff" stroke-width="0.7"/></svg>www.marlowescolombo.com</li>
    </ul>
    <address class="office">
      <div class="office__name">MARLOWE’S LIMITED</div>
      <div>12, Lotus Grove Road</div>
      <div>Colombo 00300</div>
      <div>Sri Lanka</div>
    </address>
  </section>

  <section class="card card--back">
    <h2 class="back-title">
      <span class="back-title__first">MARLOWE’S</span>
      <span class="back-title__second">ENTERTAINMENT</span>
    </h2>
    <div class="suits-art" role="img" aria-label="Faint row of playing card suit symbols"></div>
    <p class="tagline">HIGHEST WINNING PERCENTAGE IN THE WORLD</p>
  </section>
</body>
</html>
```